Design my site www.brieflyledger.com

So here is what I am thinking in terms of design:

https://plenvo.com

https://www.skyluxair.com

http://kalvex.com/harbor-plaza-tower/

I want the theme to be white and blue (royal blue). I attached a paint picture of what I would like the site to look like in terms of placing the text. Generally, what I like about the sites above is that they are simple, you can navigate easily and have some kind of idea of what's going on by looking at the center (picture and motto). Let's establish a clear understanding of how the functional part of the site would look like. Please see the picture attached.

I want to keep it simple: On top would be the Name 'BRIEFLY ledger", somewhere to the right on top on the page would be 'Sign in" button.

In the center would be a picture (maybe a video) with the Motto (on top of it all in capital) OBSERVE NAVIGATE DECIDE and below would be the "sign up now"

Below the picture (like on kalvex.com site) or to the left on top of the page would be "About Us', "Press" "Contact Us' buttons.

Then once the user gets to his page his got 3 tabs " Press Headlines", "Events", " Briefings".

we would keep the same format I only have on the site, but separate for every Tab.

I do not want the user to get distracted. I also want him to be able to access the page though mobile phone and be able to get automatic updates just like Zorvan Pings without having to sign in daily.

The landing page must be minimalist yet with business/corporate feel where users can navigate easily and a "what you see is what you get" approach. You want an image or video (personally I prefer the video.. it does capture the users attention instantly, as long as it is an interesting video), with your taglines in it.

Sections available to public: About Us, Contact Us, Landing Page with Signup Option

Private: Public Sections + User Account Page, Tabs for (Events, Press Headlines, Briefings)

Target Market(s)

PR/media monitoring/diplomatic community

Coding

Coded - Design and coding required

Number of Pages Required

1 page

Font styles to use
Serif
Sans Serif

Colors
0255a3
ec1f27

Requirements
Must have
• a simple landing page, that is user friendly.
Nice to have
• a video with the explanation of how to navigate the site
Should not have
• too many colors, graphs etc.

```html
<!DOCTYPE html>
<html lang="en">
<head>
<meta charset="utf-8">
<title>Briefly Ledger</title>
<link rel="stylesheet" href="https://fonts.googleapis.com/css2?family=Orbitron:wght@500&family=Open+Sans:wght@300;700&display=swap">
<style>
  :root {
    --white: #ffffff;
    --sky-top: #17405e;
    --sky-mid: #6a7277;
    --haze: #c89a6c;
    --city-warm: #8a6a4c;
    --city-deep: #3d3128;
    --accent-pink: #ff0a87;
    --royal-blue: #12498f;
    --rule: rgba(255, 255, 255, 0.75);
  }
  * { box-sizing: border-box; margin: 0; padding: 0; }
  html, body { width: 1200px; height: 600px; overflow: hidden; }
  body { font-family: "Open Sans", Arial, sans-serif; color: var(--white); }

  .hero {
    position: relative;
    width: 1200px;
    height: 600px;
    overflow: hidden;
  }
  .hero-backdrop {
    position: absolute;
    inset: 0;
    background:
      linear-gradient(180deg, rgba(0,0,0,0.15) 0%, rgba(0,0,0,0) 40%, rgba(0,0,0,0.25) 100%),
      linear-gradient(180deg, var(--sky-top) 0%, var(--sky-mid) 28%, var(--haze) 50%, var(--city-warm) 68%, var(--city-deep) 100%);
  }

  .brand-badge {
    position: absolute;
    left: 160px;
    top: 0;
    width: 64px;
    height: 62px;
  }
  .brand-badge svg { position: absolute; inset: 0; }
  .brand-name {
    position: absolute;
    left: 0; right: 0; top: 14px;
    text-align: center;
    font-weight: 700;
    font-size: 8.5px;
    line-height: 11px;
    letter-spacing: 0.3px;
    color: var(--royal-blue);
  }

  .top-signup {
    position: absolute;
    left: 956px;
    top: 12px;
    width: 82px;
    height: 28px;
    border: 1.5px solid var(--white);
    border-radius: 14px;
    font-weight: 700;
    font-size: 10.5px;
    letter-spacing: 0.3px;
    display: flex;
    align-items: center;
    justify-content: center;
    color: var(--white);
    text-decoration: none;
  }

  .headline {
    position: absolute;
    left: 0; right: 0;
    top: 158px;
    text-align: center;
    font-family: "Orbitron", "Arial Black", sans-serif;
    font-weight: 500;
    font-size: 44px;
    letter-spacing: 2px;
    line-height: 52px;
  }
  .tagline {
    position: absolute;
    left: 346px;
    width: 510px;
    top: 229px;
    height: 50px;
    border-top: 1px solid var(--rule);
    border-bottom: 1px solid var(--rule);
    text-align: center;
    font-weight: 300;
    font-size: 29px;
    line-height: 48px;
  }

  .cta-signup {
    position: absolute;
    left: 473px;
    top: 310px;
    width: 255px;
    height: 52px;
    border-radius: 26px;
    background: var(--accent-pink);
    color: var(--white);
    text-decoration: none;
    font-weight: 700;
    font-size: 19px;
    display: flex;
    align-items: center;
    justify-content: center;
    gap: 14px;
  }
  .cta-divider { width: 1px; height: 20px; background: var(--white); }

  .section-nav {
    position: absolute;
    top: 486px;
    left: 274px;
    display: flex;
    gap: 24px;
  }
  .section-link {
    width: 202px;
    height: 53px;
    border-radius: 27px;
    border: 1.5px solid var(--white);
    color: var(--white);
    text-decoration: none;
    font-weight: 700;
    font-size: 20px;
    display: flex;
    align-items: center;
    justify-content: center;
  }
  .section-link.is-active { background: var(--royal-blue); border-color: var(--royal-blue); }
</style>
</head>
<body>
  <main class="hero">
    <div class="hero-backdrop" role="img" aria-label="Aerial photograph of a city skyline at sunset with a tall spired skyscraper in the centre and a river in the distance"></div>

    <div class="brand-badge">
      <svg width="64" height="62" viewBox="0 0 64 62" aria-hidden="true">
        <polygon points="0,0 64,0 64,50 32,62 0,50" fill="#ffffff"/>
      </svg>
      <div class="brand-name">BRIEFLY<br>LEDGER</div>
    </div>

    <a class="top-signup" href="#">SIGN UP</a>

    <h1 class="headline">BRIEFLY LEDGER</h1>
    <p class="tagline">Observe Navigate Decide</p>

    <a class="cta-signup" href="#">
      <span>SIGN UP NOW</span>
      <span class="cta-divider"></span>
      <svg width="18" height="14" viewBox="0 0 18 14" aria-hidden="true">
        <path d="M0 7 H12" stroke="#ffffff" stroke-width="3"/>
        <polygon points="10,1 18,7 10,13" fill="#ffffff"/>
      </svg>
    </a>

    <nav class="section-nav">
      <a class="section-link is-active" href="#">ABOUT US</a>
      <a class="section-link" href="#">PRESS</a>
      <a class="section-link" href="#">CONTACT US</a>
    </nav>
  </main>
</body>
</html>
```